Home Page for a Swiss based start up company, trading Natural & Health food ingredients (B2B)

I would like to create a home page for my new start up company (Veltrana Swiss AG), the main field of activity is the trading and marketing of Natural and Health food ingredients towards the functional Food and Food supplements industry. (B2B).
Target Market : Functional Food and Food Supplement Manufacturers (B2B) based in Switzerland and Europe
The values I would like to convey are :
- sourcing of natural and health ingredients, (example : natural plant extracts, Omega 3, plant proteins, natural vitamins, vegan food ingredients...etc)
- Health & Nutritional Health
- Eco-friendly and Sustainability
- High Quality Standard in term of products and logistic services
- Trust and reliability
- Flexibility & speed to market
-Technical advice for the development of new products

The site will be translated in 3 languages (German, French, English)
Number of web pages : 5 : Home, About us, Products, Our Services, Contact

See here below attached Logo file.

Here some link of websites which can be taken as benchmark or source of inspiration
- https://quorbelix.com
- https://www.dralvimo.com/

Target Market(s)

Manufacturers of Functional Foods and Food Supplements in Switzerland and Europe (B2B)

Industry/Entity Type

B2B Trading of Natural & Health Ingredients

Coding

Number of Pages Required

Font styles to use
Sans Serif

Colors
0054AA
0677BA
7BADD7
CADEEF
E8F1F8
0094D4
00A9DD
6FCCEA
C7EBF8
E9F6FB
00AB8E
00BBA5
67D7C9
C6EFE9
E9F9F6
59FF00
82FF00
B8FF75
E3FFCB
F4FFEA
FFF300
FFF600
FEFA6F
FFFEC7
FFFEE8
FFC000
F8CF3A
FAE287
FDF2CF
FEFAEE
F0912C
F2A743
F7CA91
FBE8D2
FDF5EE
EE7325
F08F49
F5BC92
FAE3D3
FDF4ED

Requirements
Must have
• inspiration towards nature, sustainability, vegan food, functional food & beverages, food supplements, nutritional health, low carbon footprint
Should not have
• animals, chemistry, food additives

```html
<!DOCTYPE html>
<html lang="en">
<head>
<meta charset="utf-8">
<title>Veltrana Swiss – Home</title>
<link href="https://fonts.googleapis.com/css2?family=Josefin+Sans:wght@400;600;700&family=Lato:wght@400;700&display=swap" rel="stylesheet">
<style>
:root{
  --blue:#0677BA;
  --blue-deep:#0054AA;
  --blue-soft:#7BADD7;
  --orange:#EE7325;
  --orange-mid:#F08F49;
  --orange-soft:#F5BC92;
  --orange-pale:#FAE3D3;
  --ink:#222;
  --text:#333;
  --black:#000;
  --white:#fff;
}
*{margin:0;padding:0;box-sizing:border-box}
html,body{width:1200px;height:4063px;overflow:hidden;background:var(--white)}
body{position:relative;font-family:'Lato',sans-serif;color:var(--text)}
.abs{position:absolute}

/* hero */
.hero{left:0;top:0;width:1200px;height:678px;overflow:hidden}
.hero-photo{position:absolute;inset:0;background:linear-gradient(180deg,#8a8f99 0%,#a7a39a 16%,#7c6a47 24%,#b5823a 40%,#c98d3a 60%,#9a6427 85%,#6e451c 100%)}
.hero-shade{position:absolute;inset:0;background:rgba(0,0,0,.18)}
.logo{left:101px;top:40px;color:var(--white);font-family:'Josefin Sans',sans-serif;font-size:29px;font-weight:400;letter-spacing:2px;display:flex;align-items:center;gap:10px}
.logo-dot{width:10px;height:10px;border-radius:50%;background:var(--white)}
.nav{font-family:'Josefin Sans',sans-serif;font-size:17px;color:var(--white)}
.nav a{position:absolute;white-space:nowrap;color:var(--white);text-decoration:none}
.nav .active{font-weight:700}
.flag{left:911px;top:43px;width:20px;height:20px;border-radius:50%;background:#e9e9f0;border:2px solid #fff}
.quote-btn{left:963px;top:31px;width:134px;height:47px;border:2px solid var(--white);color:var(--white);font-family:'Josefin Sans',sans-serif;font-size:17px;display:flex;align-items:center;justify-content:center}
.hero-title{left:0;width:1200px;top:212px;text-align:center;color:var(--white);font-family:'Josefin Sans',sans-serif;font-weight:700;font-size:39px;letter-spacing:1px}
.hero-sub{left:0;width:1200px;top:283px;text-align:center;color:var(--white);font-family:'Josefin Sans',sans-serif;font-weight:400;font-size:32px;line-height:46px;letter-spacing:1px}
.btn-blue{left:530px;top:419px;width:140px;height:46px;background:var(--blue);color:var(--white);font-size:17px;display:flex;align-items:center;justify-content:center}
.arrow{top:322px;width:38px;height:38px;border:2px solid var(--white);border-radius:50%}
.arrow svg{display:block;width:34px;height:34px}
.wave{left:0;width:1200px}

/* about */
.photo-frame{border:4px solid var(--white);box-shadow:0 3px 12px rgba(0,0,0,.25)}
.about-title{left:621px;top:770px;font-family:'Josefin Sans',sans-serif;font-weight:400;font-size:45px;color:var(--ink);display:flex;align-items:center;gap:10px}
.accent{color:var(--blue);font-weight:700}
.title-rule{width:66px;height:2px;background:var(--ink);margin-top:20px}
.about-text{left:624px;top:836px;width:464px;font-size:16.5px;line-height:30px;text-align:justify;color:var(--text)}
.btn-orange{left:626px;top:1072px;width:142px;height:46px;background:var(--orange);color:var(--white);font-size:17px;display:flex;align-items:center;justify-content:center}

/* services */
.services{left:0;top:1224px;width:1200px;height:780px;background:linear-gradient(135deg,#2e86c4 0%,#1570b2 50%,#0c5ea6 100%)}
.section-title{left:0;width:1200px;text-align:center;font-family:'Josefin Sans',sans-serif;font-weight:400;font-size:45px;display:flex;justify-content:center;align-items:center;gap:6px}
.section-title .rule{width:66px;height:2px;margin-top:20px}
.services .section-title{color:var(--white)}
.services .section-title .rule{background:var(--white)}
.services .section-title .accent{color:var(--white)}
.services-intro{left:150px;width:900px;top:181px;text-align:center;color:var(--white);font-size:16px;line-height:30px}
.card{top:285px;width:292px;height:405px;background:var(--white)}
.card-photo{width:100%;height:206px}
.card-badge{position:absolute;left:105px;top:148px;width:82px;height:82px;border-radius:50%;background:var(--white);border:2px solid var(--blue-soft);display:flex;align-items:center;justify-content:center}
.card h3{position:absolute;top:255px;width:100%;text-align:center;font-family:'Josefin Sans',sans-serif;font-weight:600;font-size:19px;color:var(--ink)}
.card p{position:absolute;top:282px;left:26px;right:26px;text-align:center;font-size:16px;line-height:30px;color:#444}

/* values */
.value{width:214px;height:214px;border-radius:50%;border:2px dashed var(--blue-soft);display:flex;flex-direction:column;align-items:center;justify-content:center;text-align:center}
.value span{font-size:14.5px;line-height:30px;color:#333;margin-top:6px}
.value svg{width:64px;height:64px}

/* blog */
.blog{left:0;top:2801px;width:1200px;height:900px;background:linear-gradient(180deg,#ededed 0%,#f3f3f3 60%,#e9e9e9 100%)}
.blog .section-title{color:var(--ink)}
.blog .section-title .rule{background:var(--ink)}
.post{overflow:hidden}
.post-caption{position:absolute;left:35px;right:30px;color:var(--white)}
.post-date{font-size:16px;display:flex;align-items:center;gap:6px}
.post-title{font-size:18px;line-height:30px;margin-top:6px}

/* footer */
.footer{left:0;top:3660px;width:1200px;height:403px;background:var(--black);color:var(--white)}
.social{top:36px;width:38px;height:38px;border-radius:50%;background:var(--blue-soft);border:2px solid var(--orange)}
.v-rule{width:2px;background:var(--white)}
.foot-head{font-family:'Josefin Sans',sans-serif;font-weight:600;font-size:17px;top:138px}
.foot-list{font-size:15px;line-height:30px}
.foot-div{top:133px;width:1px;height:192px;background:#555}
.news-input{left:833px;top:175px;width:255px;height:46px;background:var(--white);color:#333;font-size:15px;padding-left:16px;display:flex;align-items:center}
.news-btn{left:833px;top:235px;width:99px;height:44px;background:var(--orange);color:var(--white);font-size:16px;display:flex;align-items:center;justify-content:center}
.copyright{left:832px;top:304px;font-size:14.5px}
.contact-row{display:flex;align-items:flex-start;gap:14px}
</style>
</head>
<body>

<header class="abs hero">
  <div class="hero-photo" role="img" aria-label="Golden wheat field at sunset with mountains in the distance"></div>
  <div class="hero-shade"></div>
  <div class="abs logo"><span class="logo-dot"></span>Veltrana Swiss</div>
  <nav class="abs nav" style="left:0;top:44px">
    <a class="active" style="left:366px">Home</a>
    <a style="left:448px">About</a>
    <a style="left:530px">Services</a>
    <a style="left:629px">Our Values</a>
    <a style="left:751px">Blog</a>
    <a style="left:820px">Contact</a>
  </nav>
  <div class="abs flag" aria-label="Language selector"></div>
  <div class="abs quote-btn">Get Quote</div>
  <h1 class="abs hero-title">WELCOME TO VELTRANA SWISS</h1>
  <p class="abs hero-sub">Functional Food and Food<br>Supplement Manufacturers</p>
  <div class="abs btn-blue">Learn More</div>
  <div class="abs arrow" style="left:33px"><svg viewBox="0 0 34 34"><path d="M24 17H10M15 11l-6 6 6 6" fill="none" stroke="#fff" stroke-width="2"/></svg></div>
  <div class="abs arrow" style="left:1123px"><svg viewBox="0 0 34 34"><path d="M10 17h14M19 11l6 6-6 6" fill="none" stroke="#fff" stroke-width="2"/></svg></div>
  <svg class="abs wave" style="top:578px" width="1200" height="100" viewBox="0 0 1200 100" preserveAspectRatio="none">
    <path d="M0 10 Q600 60 1200 0 V100 H0Z" fill="var(--orange-soft)"/>
    <path d="M0 35 Q600 70 1200 25 V100 H0Z" fill="var(--orange-pale)"/>
    <path d="M0 62 Q600 40 1200 62 V100 H0Z" fill="#fff"/>
  </svg>
</header>

<section>
  <div class="abs photo-frame" style="left:110px;top:757px;width:283px;height:323px;background:linear-gradient(135deg,#5a4a3a 0%,#8b6b3a 30%,#c0392b 60%,#e07a3a 80%,#7a9a3a 100%)" role="img" aria-label="Market stall with fresh fruit and vegetables"></div>
  <div class="abs photo-frame" style="left:238px;top:825px;width:282px;height:314px;background:linear-gradient(180deg,#c8c8c0 0%,#9aa08a 35%,#4f6a3c 65%,#2f4424 100%)" role="img" aria-label="Farmer inspecting leafy greens in a field"></div>
  <h2 class="abs about-title">About <span class="accent">Us</span><span class="title-rule"></span></h2>
  <p class="abs about-text">Sed ut perspiciatis unde omnis iste natus error sit lorem ip voluptatem accusantium doloremque laudantium, totam rem aperiam, eaque ipsa quae ab illo inventore veritatis et quasi architecto beatae vitae dicta sunt explicabo. Nemo enim ipsam voluptatem quia voluptas sit aspernatur aut odit aut fugit, sed quia consequuntur magni dolores eos qui ratione voluptatem sequi nesciunt.</p>
  <div class="abs btn-orange">Learn More</div>
</section>

<section class="abs services">
  <h2 class="abs section-title" style="top:92px"><span class="rule"></span>Our <span class="accent">Services</span><span class="rule"></span></h2>
  <p class="abs services-intro">Neque porro quisquam est, qui dolorem ipsum quia dolor sit amet, consectetur, adipisci velit, sed quia non numquam eius modi tempora incidunt ut labore et dolore magnam aliquam quaerat voluptatem.</p>

  <article class="abs card" style="left:126px">
    <div class="card-photo" style="background:linear-gradient(135deg,#6a4a2a,#c0532a 40%,#e0982a 60%,#a0284a 85%)" role="img" aria-label="Fresh produce at a trading market"></div>
    <div class="card-badge"><svg width="40" height="40" viewBox="0 0 40 40" fill="none" stroke="var(--orange)" stroke-width="2"><path d="M6 18h28l-3 16H9z"/><path d="M12 18l5-10M28 18l-5-10"/><path d="M14 24v6M20 24v6M26 24v6"/></svg></div>
    <h3>Trading &amp; Marketing</h3>
    <p>Neque porro quisquam est, qui dolorem ipsum quia dolor sit amet, consectetur.</p>
  </article>

  <article class="abs card" style="left:454px">
    <div class="card-photo" style="background:linear-gradient(135deg,#5a4a3a,#d0c8b8 40%,#e8e4dc 55%,#c8a030 80%,#4a3a2a)" role="img" aria-label="Warehouse with stacked sacks and a forklift"></div>
    <div class="card-badge"><svg width="42" height="40" viewBox="0 0 42 40" fill="none" stroke="var(--orange)" stroke-width="2"><rect x="4" y="10" width="22" height="16"/><path d="M26 15h7l5 6v5H26z"/><circle cx="12" cy="29" r="3"/><circle cx="32" cy="29" r="3"/><path d="M11 17l3 3 6-6"/></svg></div>
    <h3>Transportation</h3>
    <p>Neque porro quisquam est, qui dolorem ipsum quia dolor sit amet, consectetur.</p>
  </article>

  <article class="abs card" style="left:782px">
    <div class="card-photo" style="background:linear-gradient(135deg,#e8eef2,#cdd6dc 45%,#c8a87a 75%,#a8845a)" role="img" aria-label="Workers packing boxes in a clean facility"></div>
    <div class="card-badge"><svg width="40" height="40" viewBox="0 0 40 40" fill="none" stroke="var(--orange)" stroke-width="2"><path d="M6 12l14-6 14 6v16l-14 6-14-6z"/><path d="M6 12l14 6 14-6M20 18v16"/><circle cx="30" cy="29" r="5"/><path d="M28 29l2 2 3-3"/></svg></div>
    <h3>Logistics</h3>
    <p>Neque porro quisquam est, qui dolorem ipsum quia dolor sit amet, consectetur.</p>
  </article>
</section>

<section>
  <h2 class="abs section-title" style="top:2093px;color:var(--ink)"><span class="rule" style="background:var(--ink)"></span>Our <span class="accent">Values</span><span class="rule" style="background:var(--ink)"></span></h2>

  <div class="abs value" style="left:112px;top:2214px">
    <svg viewBox="0 0 64 64" fill="none" stroke="var(--orange)" stroke-width="2"><path d="M14 30h36l-4 22H18z"/><path d="M22 30c0-10 4-16 10-18 6 2 10 8 10 18"/><path d="M24 38v8M32 38v8M40 38v8"/></svg>
    <span>Sourcing of natural<br>&amp; health ingredients</span>
  </div>
  <div class="abs value" style="left:366px;top:2214px">
    <svg viewBox="0 0 64 64" fill="none" stroke="var(--orange)" stroke-width="2"><path d="M32 30c-6-8-16-4-12 4l12 10 12-10c4-8-6-12-12-4z"/><path d="M10 32v14l12 8M54 32v14l-12 8"/></svg>
    <span>Health &amp; Nutritional<br>Health</span>
  </div>
  <div class="abs value" style="left:620px;top:2214px">
    <svg viewBox="0 0 64 64" fill="none" stroke="var(--orange)" stroke-width="2"><circle cx="32" cy="32" r="20"/><circle cx="32" cy="32" r="13"/><path d="M25 28c4-2 6 2 10 0s4 6 2 8-6 0-8 4"/></svg>
    <span>Eco-friendly and<br>Sustainability</span>
  </div>
  <div class="abs value" style="left:874px;top:2214px">
    <svg viewBox="0 0 64 64" fill="none" stroke="var(--orange)" stroke-width="2"><circle cx="32" cy="26" r="16"/><path d="M24 40l-4 16 12-6 12 6-4-16"/><path d="M25 26l5 5 9-9"/></svg>
    <span>High Quality<br>Standard</span>
  </div>

  <div class="abs value" style="left:112px;top:2468px">
    <svg viewBox="0 0 64 64" fill="none" stroke="var(--orange)" stroke-width="2"><circle cx="32" cy="16" r="8"/><path d="M28 16l3 3 5-5"/><path d="M8 36l10-8 10 4 8-2 10-2 10 8-12 12-8-4-6 4z"/></svg>
    <span>Trust and reliability</span>
  </div>
  <div class="abs value" style="left:366px;top:2468px">
    <svg viewBox="0 0 64 64" fill="none" stroke="var(--orange)" stroke-width="2"><circle cx="36" cy="34" r="18"/><path d="M36 22v12l8 4M32 12h8M6 28h10M4 36h10M8 44h10"/></svg>
    <span>Flexibility &amp; speed<br>to market</span>
  </div>
  <div class="abs value" style="left:620px;top:2468px">
    <svg viewBox="0 0 64 64" fill="none" stroke="var(--orange)" stroke-width="2"><circle cx="32" cy="20" r="10"/><circle cx="32" cy="20" r="4"/><path d="M8 44h14l10 4 14-6 8 4-14 10H10z"/></svg>
    <span>Technical advice for<br>the development</span>
  </div>
  <div class="abs value" style="left:874px;top:2468px">
    <svg viewBox="0 0 64 64" fill="none" stroke="var(--orange)" stroke-width="2"><path d="M32 8l20 8v14c0 14-10 22-20 26-10-4-20-12-20-26V16z"/><path d="M23 32l7 7 12-12"/></svg>
    <span>security of supplyd</span>
  </div>
</section>

<section class="abs blog">
  <h2 class="abs section-title" style="top:88px"><span class="rule"></span>Latest <span class="accent">Blog</span><span class="rule"></span></h2>

  <article class="abs post" style="left:110px;top:216px;width:489px;height:473px">
    <div style="position:absolute;inset:0;background:linear-gradient(160deg,#2f6b2a 0%,#4f9a3c 40%,#3a7a30 70%,#1e4a1c 100%)" role="img" aria-label="Aerial view of forest with footprint-shaped clearing"></div>
    <div style="position:absolute;inset:0;background:linear-gradient(180deg,rgba(0,0,0,0) 50%,rgba(0,0,0,.55) 100%)"></div>
    <div class="post-caption" style="top:346px">
      <div class="post-date">27 April 2022 <svg width="16" height="16" viewBox="0 0 16 16" fill="none" stroke="#fff" stroke-width="1.5"><rect x="2" y="3" width="12" height="11"/><path d="M2 7h12M5 1v4M11 1v4"/></svg></div>
      <div class="post-title">Neque porro quisquam est, qui dolorem ipsum quia dolor sit amet, consectetur.</div>
    </div>
  </article>

  <article class="abs post" style="left:612px;top:216px;width:476px;height:228px">
    <div style="position:absolute;inset:0;background:linear-gradient(135deg,#4a3020 0%,#7a5030 35%,#e8e4d8 60%,#5a7a30 80%,#3a2418 100%)" role="img" aria-label="Nuts, seeds and tofu on a wooden table"></div>
    <div style="position:absolute;inset:0;background:linear-gradient(180deg,rgba(0,0,0,0) 40%,rgba(0,0,0,.55) 100%)"></div>
    <div class="post-caption" style="top:143px">
      <div class="post-date">27 April 2022 <svg width="16" height="16" viewBox="0 0 16 16" fill="none" stroke="#fff" stroke-width="1.5"><rect x="2" y="3" width="12" height="11"/><path d="M2 7h12M5 1v4M11 1v4"/></svg></div>
      <div class="post-title">Neque porro quisquam est, qui dolorem</div>
    </div>
  </article>

  <article class="abs post" style="left:612px;top:459px;width:476px;height:230px">
    <div style="position:absolute;inset:0;background:linear-gradient(135deg,#a8c88a 0%,#6a9a3a 30%,#d06a2a 60%,#e8872a 75%,#f0f0ea 100%)" role="img" aria-label="Fresh vegetables and a glass of orange juice"></div>
    <div style="position:absolute;inset:0;background:linear-gradient(180deg,rgba(0,0,0,0) 40%,rgba(0,0,0,.55) 100%)"></div>
    <div class="post-caption" style="top:145px">
      <div class="post-date">27 April 2022 <svg width="16" height="16" viewBox="0 0 16 16" fill="none" stroke="#fff" stroke-width="1.5"><rect x="2" y="3" width="12" height="11"/><path d="M2 7h12M5 1v4M11 1v4"/></svg></div>
      <div class="post-title">Neque porro quisquam est, qui dolorem</div>
    </div>
  </article>
</section>

<svg class="abs wave" style="top:3585px" width="1200" height="90" viewBox="0 0 1200 90" preserveAspectRatio="none">
  <path d="M0 0 Q600 40 1200 0 V90 H0Z" fill="var(--orange-pale)"/>
  <path d="M0 18 Q600 60 1200 18 V90 H0Z" fill="var(--orange-soft)"/>
  <path d="M0 50 L600 38 L1200 50 V90 H0Z" fill="var(--orange-mid)"/>
</svg>

<footer class="abs footer">
  <div class="abs v-rule" style="left:462px;top:33px;height:42px"></div>
  <div class="abs v-rule" style="left:733px;top:33px;height:42px"></div>
  <div class="abs social" style="left:497px" aria-label="Social profile link"></div>
  <div class="abs social" style="left:553px" aria-label="Social profile link"></div>
  <div class="abs social" style="left:609px" aria-label="Social profile link"></div>
  <div class="abs social" style="left:664px" aria-label="Social profile link"></div>

  <div class="abs foot-head" style="left:114px">Contact us</div>
  <div class="abs foot-list" style="left:112px;top:170px">
    <div class="contact-row"><svg width="18" height="22" viewBox="0 0 18 22"><path d="M9 1C4.6 1 2 4.2 2 8c0 5 7 13 7 13s7-8 7-13c0-3.8-2.6-7-7-7z" fill="var(--orange)"/><circle cx="9" cy="8" r="2.6" fill="#000"/></svg><span>Veltrana Swiss,<br>Address comes here</span></div>
    <div class="contact-row" style="margin-top:16px"><svg width="18" height="18" viewBox="0 0 18 18"><path d="M4 1l3 4-2 2c1 2.5 3.5 5 6 6l2-2 4 3-2 3C8 17 1 10 1 3z" fill="var(--orange)"/></svg><span>+41 44 555 0182</span></div>
    <div class="contact-row" style="margin-top:16px"><svg width="18" height="14" viewBox="0 0 18 14"><rect x="1" y="1" width="16" height="12" fill="var(--orange)"/><path d="M1 2l8 6 8-6" fill="none" stroke="#000" stroke-width="1.5"/></svg><span>info@veltranaswiss.com</span></div>
  </div>

  <div class="abs foot-div" style="left:345px"></div>
  <div class="abs foot-head" style="left:416px">Quick link</div>
  <div class="abs foot-list" style="left:417px;top:170px">Home<br>About<br>Services<br>Our Value<br>Blog</div>

  <div class="abs foot-div" style="left:560px"></div>
  <div class="abs foot-head" style="left:623px">Others</div>
  <div class="abs foot-list" style="left:624px;top:170px">Case Study<br>FAQs<br>Contact Us</div>

  <div class="abs foot-div" style="left:762px"></div>
  <div class="abs foot-head" style="left:834px">Newsletter</div>
  <div class="abs news-input">Learn More</div>
  <div class="abs news-btn">Submit</div>
  <div class="abs copyright">2022 Veltrana Swiss. All Rights Reserved.</div>
</footer>

</body>
</html>
```